I want a website to be designed for our new company, it's an import and export company for variety of things.

please see the attached Logo for our company and the Images for our different sections for our busienss

Target Market(s)

multiple

Coding

Coded - Design and coding required

Number of Pages Required

5+ page

Font styles to use
Sans Serif

Colors

Designer to choose colors to be used in the design.

Requirements
Must have
• KVR GLOBALINKS
• KVR globalinks Trading & Contracting provides various services. The Company offers infrastructure construction, oil, enegy and gas services, agricultural projects, real estate development, travel and tourism, and food processing and trading.
• Civil contracting for infrastructure, residential and heavy projects. Through its main subsidiaries; distribution of general food products, construction chemicals including corrosion inhibitors and electrical machinery; provides catering and travel agency services; ownership and operation of a school; offers human sources services including manpower supply.
• Drilling and Gold Mines Used Machinery, All Kinds of Construction Machinery, Drilling Machines are manufactured and sold.
Nice to have
• good designa and beautiful colours, it has too look professional

```html
<!DOCTYPE html>
<html lang="en">
<head>
<meta charset="utf-8">
<title>KVR GLOBALINKS – Trading &amp; Contracting</title>
<link rel="stylesheet" href="https://fonts.googleapis.com/css2?family=Roboto:wght@400;500;700;900&family=Open+Sans:ital,wght@0,400;0,600;1,400&display=swap">
<style>
:root{
  --black:#0d0d0d;
  --panel:#141414;
  --gold:#b5782c;
  --white:#ffffff;
  --ink:#1b1b1b;
  --muted:#555;
  --grey-band:#e6e6e6;
  --news-grey:#a0a7b1;
  --accordion:#8a8a8a;
  --footer:#0b0b0b;
}
*{box-sizing:border-box;margin:0;padding:0}
html,body{width:1200px;height:3954px;overflow:hidden}
body{position:relative;background:var(--white);font-family:"Open Sans",sans-serif;color:var(--ink)}
.abs{position:absolute}
.heading{font-family:"Roboto",sans-serif;font-weight:700;text-transform:uppercase}
.btn{position:absolute;background:var(--gold);color:var(--white);font-family:"Roboto",sans-serif;font-weight:700;text-transform:uppercase;display:flex;align-items:center;justify-content:center}

/* header */
.site-header{position:absolute;left:0;top:0;width:1200px;height:127px;background:var(--black)}
.brand{position:absolute;left:129px;top:42px;display:flex;align-items:center;gap:10px;color:var(--white);font-family:"Roboto",sans-serif;font-weight:500;font-size:20px;letter-spacing:2px}
.brand-dot{width:14px;height:14px;border-radius:50%;background:var(--gold)}
.contact-chip{position:absolute;top:26px;display:flex;gap:14px;color:var(--white)}
.contact-chip small{display:block;font-family:"Roboto",sans-serif;font-size:11px;font-weight:500;text-transform:uppercase}
.contact-chip span{font-size:14px}
.contact-chip .big{font-family:"Roboto",sans-serif;font-size:20px;font-weight:500}
.main-nav{position:absolute;top:86px;left:496px;display:flex;gap:0;font-family:"Roboto",sans-serif;font-weight:500;font-size:15px;color:var(--white);text-transform:uppercase}
.main-nav a{color:inherit;text-decoration:none;height:26px;display:flex;align-items:center;padding:0 10px;margin-right:16px}
.main-nav a.active{background:var(--gold)}
.main-nav a:last-child{margin-right:0}

/* hero */
.hero{position:absolute;left:0;top:127px;width:1200px;height:533px;background:linear-gradient(180deg,#1b2c4d 0%,#2f5a8c 40%,#1e4a7a 70%,#0e2848 100%)}
.hero-rig{position:absolute;left:600px;top:0;width:600px;height:533px;background:radial-gradient(ellipse at 55% 50%,#b88a3a 0%,#5a4a3a 30%,rgba(30,60,100,0) 65%)}
.hero-title{position:absolute;left:134px;top:142px;color:var(--white);font-family:"Roboto",sans-serif;font-weight:900;font-size:54px;line-height:57px;letter-spacing:1px;text-transform:uppercase}
.hero .btn{left:140px;top:344px;width:135px;height:40px;font-size:17px}
.hero-dots{position:absolute;left:549px;top:481px;display:flex;gap:14px}
.hero-dots i{width:9px;height:9px;border-radius:50%;background:var(--white)}
.hero-dots i.on{background:var(--gold)}

/* section headings */
.section-title{position:absolute;left:0;width:1200px;text-align:center;font-family:"Roboto",sans-serif;font-weight:700;font-size:26px;color:var(--ink);text-transform:uppercase}
.title-rule{position:absolute;left:560px;width:80px;height:3px;background:var(--gold)}

/* services */
.service{position:absolute;width:301px;height:233px}
.service .photo{position:absolute;inset:0}
.service .caption{position:absolute;left:21px;bottom:-25px;width:260px;height:50px;background:var(--white);display:flex;align-items:center;justify-content:space-between;padding:0 20px 0 13px;font-family:"Roboto",sans-serif;font-weight:500;font-size:13px;line-height:17px;text-transform:uppercase}
.more{background:var(--gold);color:var(--white);font-family:"Roboto",sans-serif;font-weight:700;font-size:11px;padding:4px 8px;text-transform:uppercase}
.service .caption-open{position:absolute;left:17px;top:85px;width:284px;height:155px;background:var(--white);padding:20px 22px}
.caption-open .row{display:flex;justify-content:space-between;font-family:"Roboto",sans-serif;font-weight:500;font-size:13px;line-height:17px;text-transform:uppercase}
.caption-open p{margin-top:22px;font-size:11.5px;line-height:16px;color:var(--muted)}

/* why choose us */
.why-photo{position:absolute;left:0;top:1420px;width:599px;height:517px;background:linear-gradient(180deg,#33475f 0%,#6b6b6a 45%,#4a6a2a 80%,#2e4a1a 100%)}
.why-panel{position:absolute;left:599px;top:1420px;width:601px;height:517px;background:var(--panel);color:var(--white)}
.why-panel h2{position:absolute;left:41px;top:88px;font-size:26px}
.why-panel .lead{position:absolute;left:41px;top:135px;width:430px;font-size:13.5px;line-height:19px;color:#ddd}
.acc{position:absolute;left:41px;width:427px;height:31px;background:var(--accordion);color:var(--white);font-family:"Roboto",sans-serif;font-size:12.5px;display:flex;align-items:center;justify-content:space-between;padding:0 16px;text-transform:uppercase}
.acc.open{background:var(--gold)}
.acc-body{position:absolute;left:41px;top:233px;width:427px;height:109px;background:var(--white);color:var(--muted);font-size:11.5px;line-height:16px;padding:12px 22px}

/* news */
.news-band{position:absolute;left:0;top:1937px;width:1200px;height:573px;background:var(--grey-band)}
.news-lead{position:absolute;left:23px;top:2105px;width:456px;height:347px;background:var(--news-grey);color:var(--white);padding:52px 46px}
.news-lead time{font-size:12px;font-style:italic}
.news-lead h3{margin-top:14px;font-size:22px;line-height:30px;font-family:"Roboto",sans-serif;font-weight:700;text-transform:uppercase}
.news-lead p{margin-top:14px;font-size:12.5px;line-height:19px}
.news-lead .btn{left:46px;top:263px;width:104px;height:29px;font-size:12px}
.news-card{position:absolute;top:2105px;width:281px;height:347px;overflow:hidden}
.news-card .top{position:absolute;left:0;top:0;width:100%;height:139px;background:#1e2736;padding:22px 22px;color:var(--white)}
.news-card h4{font-family:"Roboto",sans-serif;font-weight:700;font-size:16px;line-height:22px;text-transform:uppercase}
.news-card .more{display:inline-block;margin-top:12px;font-size:11.5px;padding:5px 13px}
.news-card .photo{position:absolute;left:0;top:139px;width:100%;height:208px}
.slider-arrow{position:absolute;width:34px;height:34px;border-radius:50%;background:var(--white);display:flex;align-items:center;justify-content:center}

/* projects */
.project{position:absolute;top:2683px;width:253px;height:387px;color:var(--white)}
.project h4{position:absolute;left:22px;top:22px;width:215px;font-family:"Roboto",sans-serif;font-weight:500;font-size:16px;line-height:24px;text-transform:uppercase}
.project .tag{position:absolute;left:10px;bottom:24px;transform:rotate(-90deg);transform-origin:left top;top:auto;font-family:"Roboto",sans-serif;font-weight:700;font-size:16px;text-transform:uppercase;white-space:nowrap}

/* drilling */
.drilling{position:absolute;left:0;top:3134px;width:1200px;height:409px;background:linear-gradient(90deg,#3b2a20 0%,#5a3f2d 50%,#4a3324 100%);color:var(--white)}
.drilling h2{position:absolute;left:195px;top:78px;font-family:"Roboto",sans-serif;font-weight:900;font-size:38px;line-height:46px;text-transform:uppercase}
.drilling p{position:absolute;left:197px;top:180px;width:440px;font-size:18px;line-height:25px}
.drilling .btn{left:201px;top:285px;width:132px;height:38px;font-size:15px}

/* footer */
.site-footer{position:absolute;left:0;top:3543px;width:1200px;height:411px;background:var(--footer);color:var(--white)}
.footer-brand{position:absolute;left:129px;top:100px;display:flex;align-items:center;gap:12px;font-family:"Roboto",sans-serif;font-weight:500;font-size:26px;letter-spacing:2px}
.footer-col{position:absolute;top:66px}
.footer-col h5{font-family:"Roboto",sans-serif;font-weight:700;font-size:16px;text-transform:uppercase;margin-bottom:24px}
.footer-menu li{list-style:none;font-size:14px;line-height:24px;text-transform:uppercase}
.footer-item{display:flex;gap:14px;align-items:flex-start;margin-bottom:22px;font-size:14px;line-height:19px}
.footer-item .ic{width:28px;height:28px;border-radius:50%;background:var(--white);flex:none;display:flex;align-items:center;justify-content:center}
.footer-rule{position:absolute;left:129px;top:324px;width:942px;height:1px;background:#333}
.copyright{position:absolute;left:0;top:360px;width:1200px;text-align:center;font-size:11px;color:#ccc}
</style>
</head>
<body>

<header class="site-header">
  <div class="brand"><span class="brand-dot"></span>KVR GLOBALINKS</div>
  <div class="contact-chip" style="left:640px">
    <svg width="30" height="30" viewBox="0 0 24 24" fill="none" stroke="#fff" stroke-width="1.5"><path d="M5 3h4l2 5-2.5 1.5a11 11 0 0 0 6 6L16 13l5 2v4a2 2 0 0 1-2 2A16 16 0 0 1 3 5a2 2 0 0 1 2-2z"/></svg>
    <div><small>E mail us</small><span>info@kvrglobalinks.com</span></div>
  </div>
  <div class="contact-chip" style="left:900px">
    <svg width="30" height="24" viewBox="0 0 26 20" fill="none" stroke="#fff" stroke-width="1.5"><rect x="1" y="1" width="24" height="18"/><path d="M1 1l12 10L25 1"/></svg>
    <div><small>Call us now</small><span class="big">888.888.8888</span></div>
  </div>
  <nav class="main-nav">
    <a class="active">Home</a><a>About us</a><a>Services</a><a>Projects</a><a>News</a><a>Contact us</a>
  </nav>
</header>

<section class="hero">
  <div class="hero-rig" role="img" aria-label="Offshore oil platform lit up at dusk over the sea"></div>
  <h1 class="hero-title">Trading &amp;<br>Contracting<br>Services</h1>
  <a class="btn">Read more</a>
  <div class="hero-dots"><i></i><i></i><i class="on"></i><i></i><i></i></div>
</section>

<section class="services">
  <div class="title-rule" style="top:740px"></div>
  <h2 class="section-title" style="top:757px">Our Services</h2>

  <div class="service" style="left:129px;top:817px">
    <div class="photo" role="img" aria-label="Construction workers on steel framing at sunset" style="background:linear-gradient(180deg,#2d3b4a,#c9782d 60%,#1f1a14)"></div>
    <div class="caption"><span>Infrastructure<br>construction</span><span class="more">More</span></div>
  </div>
  <div class="service" style="left:450px;top:817px">
    <div class="photo" role="img" aria-label="Gas plant chimneys against a pink sky" style="background:linear-gradient(180deg,#c98a7a,#e0a07a 55%,#3a3340)"></div>
    <div class="caption-open">
      <div class="row"><span>Oil, enegy and<br>gas services</span><span class="more" style="align-self:flex-start">More</span></div>
      <p>If you are going to use a passage of Lorem Ipsum, you need to be sure there isn't anything embarrassing hidden in the middle of text.</p>
    </div>
  </div>
  <div class="service" style="left:768px;top:817px">
    <div class="photo" role="img" aria-label="Combine harvester in a wheat field" style="background:linear-gradient(180deg,#7fa6cf,#c8b07a 50%,#8c6a32)"></div>
    <div class="caption"><span>Agricultural<br>projects</span><span class="more">More</span></div>
  </div>
  <div class="service" style="left:129px;top:1096px">
    <div class="photo" role="img" aria-label="Suburban family houses at dusk" style="background:linear-gradient(180deg,#d0603a,#6a6470 45%,#3a3a3a)"></div>
    <div class="caption"><span>Real estate<br>development</span><span class="more">More</span></div>
  </div>
  <div class="service" style="left:450px;top:1096px">
    <div class="photo" role="img" aria-label="Traveller in a boat on a turquoise lagoon" style="background:linear-gradient(180deg,#4a6a5a,#2f8a8a 50%,#7a4a2a)"></div>
    <div class="caption"><span>Travel and<br>tourism</span><span class="more">More</span></div>
  </div>
  <div class="service" style="left:768px;top:1096px">
    <div class="photo" role="img" aria-label="Food processing plant with steel tanks" style="background:linear-gradient(180deg,#8aa0b5,#c7d2dc 50%,#6a7a88)"></div>
    <div class="caption"><span>Food processing<br>and trading</span><span class="more">More</span></div>
  </div>
</section>

<section class="why">
  <div class="why-photo" role="img" aria-label="Large lit family house with a green lawn at evening"></div>
  <div class="why-panel">
    <div class="title-rule" style="left:41px;top:70px"></div>
    <h2 class="heading">Why choose us</h2>
    <p class="lead">There are many variations of passages of Lorem Ipsum available, but the majority have suffered alteration in some form.</p>
    <div class="acc open" style="top:201px"><span>Mission</span>
      <svg width="12" height="8" viewBox="0 0 12 8" fill="none" stroke="#fff" stroke-width="2"><path d="M1 1l5 5 5-5"/></svg></div>
    <div class="acc-body">If you are going to use a passage of Lorem Ipsum, you need to be sure there isn't anything embarrassing hidden in the middle of text. All the Lorem Ipsum generators on the Internet tend to repeat predefined chunks as necessary, making this the first true generator on the Internet</div>
    <div class="acc" style="top:357px"><span>Vision</span><svg width="12" height="8" viewBox="0 0 12 8" fill="none" stroke="#fff" stroke-width="2"><path d="M1 1l5 5 5-5"/></svg></div>
    <div class="acc" style="top:399px"><span>Core values</span><svg width="12" height="8" viewBox="0 0 12 8" fill="none" stroke="#fff" stroke-width="2"><path d="M1 1l5 5 5-5"/></svg></div>
    <div class="acc" style="top:441px"><span>Quality</span><svg width="12" height="8" viewBox="0 0 12 8" fill="none" stroke="#fff" stroke-width="2"><path d="M1 1l5 5 5-5"/></svg></div>
  </div>
</section>

<section class="news-band">
  <div class="title-rule" style="top:60px"></div>
  <h2 class="section-title" style="top:98px">Latest News</h2>
</section>
<article class="news-lead">
  <time>18 Jan,2019</time>
  <h3>Contrary to popular belief Lorem Ipsum is not simply</h3>
  <p>If you are going to use a passage of Lorem Ipsum, you need to be sure there isn't anything emb arrassing hidden in the middle of text. All the Lorem Ipsum generators</p>
  <a class="btn">Read more</a>
</article>
<article class="news-card" style="left:491px">
  <div class="top"><h4>Contrary to popular belief Lorem Ipsum is not simply</h4><span class="more">Read more</span></div>
  <div class="photo" role="img" aria-label="City bridge over a river at dusk" style="background:linear-gradient(180deg,#3a4a6a,#7a6a5a 50%,#2a3a4a)"></div>
</article>
<article class="news-card" style="left:778px">
  <div class="top"><h4>Contrary to popular belief Lorem Ipsum is not simply</h4><span class="more">Read more</span></div>
  <div class="photo" role="img" aria-label="Oil pump jack in a desert landscape" style="background:linear-gradient(180deg,#c9d3dc,#8a8a84 55%,#5a4a3a)"></div>
</article>
<article class="news-card" style="left:1067px;width:133px">
  <div class="top"><h4>Contrary to popular belief Lorem Ipsum is not simply</h4><span class="more">Read more</span></div>
  <div class="photo" role="img" aria-label="Building construction site with cranes at sunset" style="background:linear-gradient(180deg,#e09a4a,#a0602a 60%,#3a2a1a)"></div>
</article>
<div class="slider-arrow" style="left:8px;top:2261px"><svg width="10" height="16" viewBox="0 0 10 16" fill="none" stroke="#222" stroke-width="2.5"><path d="M8 2L2 8l6 6"/></svg></div>
<div class="slider-arrow" style="left:1146px;top:2261px"><svg width="10" height="16" viewBox="0 0 10 16" fill="none" stroke="#222" stroke-width="2.5"><path d="M2 2l6 6-6 6"/></svg></div>

<section class="projects">
  <div class="title-rule" style="top:2594px"></div>
  <h2 class="section-title" style="top:2615px">Our Projects</h2>
  <div class="project" style="left:97px" role="img" aria-label="Workers in safety vests by scaffolding"><div class="abs" style="inset:0;background:linear-gradient(180deg,#5a6070,#9a8a70 50%,#6a4030)"></div><h4>Lorem ipsum you need to be sure there.</h4><span class="tag">Lorem ipsum</span></div>
  <div class="project" style="left:350px" role="img" aria-label="City skyline at night"><div class="abs" style="inset:0;background:linear-gradient(180deg,#3a4050,#5a5a50 50%,#2a2a2a)"></div><h4>Lorem ipsum you need to be sure there.</h4><span class="tag">Lorem ipsum</span></div>
  <div class="project" style="left:603px" role="img" aria-label="Combine harvester in a grain field"><div class="abs" style="inset:0;background:linear-gradient(180deg,#6a7a8a,#9a7a40 55%,#6a4a1a)"></div><h4>Lorem ipsum you need to be sure there.</h4><span class="tag">Lorem ipsum</span></div>
  <div class="project" style="left:854px" role="img" aria-label="Traveller with a sun hat facing a tropical island"><div class="abs" style="inset:0;background:linear-gradient(180deg,#5a7a80,#3a8a8a 55%,#2a5a6a)"></div><h4>Lorem ipsum you need to be sure there.</h4><span class="tag">Lorem ipsum</span></div>
  <svg class="abs" style="left:44px;top:2866px" width="14" height="24" viewBox="0 0 14 24" fill="none" stroke="#333" stroke-width="2.5"><path d="M12 2L2 12l10 10"/></svg>
  <svg class="abs" style="left:1137px;top:2866px" width="14" height="24" viewBox="0 0 14 24" fill="none" stroke="#333" stroke-width="2.5"><path d="M2 2l10 10-10 10"/></svg>
</section>

<section class="drilling" role="img" aria-label="Drilling auger boring into brown soil">
  <h2>Drilling and<br>gold mines</h2>
  <p>If you are going to use a passage of Lorem Ipsum, you need to be sure there isn't anything emb arrassing hidden in the middle of text.</p>
  <a class="btn">Read more</a>
</section>

<footer class="site-footer">
  <div class="footer-brand"><span class="brand-dot" style="width:18px;height:18px"></span>KVR GLOBALINKS</div>
  <div class="footer-col" style="left:491px">
    <h5>Menu</h5>
    <ul class="footer-menu"><li>Home</li><li>About us</li><li>Services</li><li>Projects</li><li>News</li><li>Contact us</li></ul>
  </div>
  <div class="footer-col" style="left:657px">
    <h5>Contact us</h5>
    <div class="footer-item"><span class="ic"><svg width="12" height="14" viewBox="0 0 12 16"><path d="M6 0a6 6 0 0 1 6 6c0 4-6 10-6 10S0 10 0 6a6 6 0 0 1 6-6z" fill="#111"/><circle cx="6" cy="6" r="2" fill="#fff"/></svg></span><span>2150 Harbor Point Road<br>Linden, CA 90412</span></div>
    <div class="footer-item"><span class="ic"><svg width="12" height="12" viewBox="0 0 24 24"><path d="M5 3h4l2 5-2.5 1.5a11 11 0 0 0 6 6L16 13l5 2v4a2 2 0 0 1-2 2A16 16 0 0 1 3 5a2 2 0 0 1 2-2z" fill="#111"/></svg></span><span>Call Us<br>888.888.8888</span></div>
    <div class="footer-item"><span class="ic"><svg width="12" height="10" viewBox="0 0 26 20"><rect x="1" y="1" width="24" height="18" fill="#111"/><path d="M1 1l12 10L25 1" stroke="#fff" stroke-width="2" fill="none"/></svg></span><span>E mail Us<br>info@kvrglobalinks.com</span></div>
  </div>
  <div class="footer-col" style="left:944px">
    <h5>Follow us</h5>
    <div class="footer-item"><span class="ic"></span><span>Like us on<br>FRIENDSPACE</span></div>
    <div class="footer-item"><span class="ic"></span><span>Follow us on<br>CHIRPLINE</span></div>
    <div class="footer-item"><span class="ic"></span><span>Follow us on<br>WORKNET</span></div>
  </div>
  <div class="footer-rule"></div>
  <p class="copyright">Copyright © 2020 All Rights Reserved</p>
</footer>

</body>
</html>
```